Dietitian needs awesome business card

I need a contemporary design that's eye catching but professional.
My card is to given to doctors, specialists and patients alike.
I manage patients with chronic diseases
I have uploaded my logo and current business card, I would also like the other Certified Clinical Nutritionist logo incorporated into the design

Target Market(s)

Doctors, specialists and patients

Industry/Entity Type

Healthcare

Contact Information for Business Card

www.brightfieldnutrition.com.au
Ph: 0427 561 903
Fax: 6457 2183
email: marcus.k.diet@fernmail.com
Space on the back of the card with: Appointment date, Appointment time and appointment location

Font styles to use
Serif

Colors
fbee3e
876aae
ffc214

Requirements
Must have
• My Logo
• Certified Clinical Nutritionist Logo
• My 4 locations - Pinebrook Medical Centre, North Corrin Health, Hollis Medical, Ashcombe Doctors Surgery
Nice to have
• I like the colours in my current business card

```html
<!DOCTYPE html>
<html lang="en">
<head>
<meta charset="utf-8">
<title>Brightfield Nutrition &amp; Dietetics – Business Card</title>
<link rel="stylesheet" href="https://fonts.googleapis.com/css2?family=Open+Sans:wght@400;700&family=Tinos&display=swap">
<style>
  :root {
    --bg: #2f2b29;
    --card-black: #0c0c0c;
    --card-white: #ffffff;
    --leaf-green: #6fbe27;
    --lime: #8cc63f;
    --brand-blue: #2f5fb3;
    --text-white: #f2f2f2;
    --text-grey: #bdbdbd;
    --text-dark: #222222;
    --accent-orange: #f26a1b;
    --rule: #555555;
  }
  * { box-sizing: border-box; margin: 0; padding: 0; }
  html, body { width: 1200px; height: 900px; overflow: hidden; }
  body {
    background: var(--bg);
    font-family: "Open Sans", Arial, sans-serif;
    position: relative;
  }
  .card {
    position: absolute;
    width: 540px;
    height: 330px;
    top: 285px;
    border-radius: 4px;
    overflow: hidden;
    box-shadow: 0 10px 28px rgba(0,0,0,.45);
  }

  /* Brand lockup */
  .brand {
    position: absolute;
    display: flex;
    align-items: center;
    gap: 14px;
  }
  .brand-dot { width: 70px; height: 70px; border-radius: 50%; flex: none; }
  .brand-name { font-weight: 400; line-height: 1.05; }
  .brand-name .brand-main { display: block; font-size: 36px; }
  .brand-name .brand-sub { display: block; font-size: 17px; padding-left: 14px; }

  /* Front */
  .card-front { left: 40px; background: var(--card-black); color: var(--text-white); }
  .card-front .brand { left: 30px; top: 56px; }
  .card-front .brand-dot { background: var(--lime); }
  .card-front .brand-name { color: var(--brand-blue); }

  .contact-list {
    position: absolute;
    right: 30px;
    top: 150px;
    list-style: none;
    font-size: 13px;
    line-height: 19px;
  }
  .contact-list li { display: flex; justify-content: flex-end; align-items: center; gap: 7px; }
  .contact-list svg { width: 11px; height: 11px; fill: var(--lime); flex: none; }
  .contact-list .gap { margin-top: 16px; }

  .person { position: absolute; left: 30px; top: 226px; }
  .person-name { color: var(--lime); font-weight: 700; font-size: 17px; }
  .person-role { font-size: 13px; color: var(--text-white); }

  .credential {
    position: absolute;
    left: 30px; bottom: 20px;
    font-family: "Tinos", "Times New Roman", serif;
    font-size: 21px;
    color: var(--lime);
  }

  /* Back */
  .card-back { left: 620px; background: var(--card-white); }
  .back-band {
    position: absolute; left: 0; top: 0; width: 100%; height: 150px;
    background: var(--leaf-green);
  }
  .card-back .brand { left: 30px; top: 40px; }
  .card-back .brand-dot { background: var(--card-white); }
  .card-back .brand-name { color: var(--card-white); }

  .badge-block {
    position: absolute; right: 24px; top: 160px;
    display: flex; align-items: center; gap: 14px;
  }
  .badge-text {
    color: var(--accent-orange);
    font-size: 11px; line-height: 1.3; text-align: center;
  }
  .badge-shape { width: 30px; height: 30px; background: var(--accent-orange); }

  .appointment {
    position: absolute; left: 30px; top: 158px;
    list-style: none;
    font-size: 15px; color: var(--text-dark);
  }
  .appointment li { display: flex; align-items: flex-end; height: 30px; }
  .appointment .line {
    display: inline-block; width: 230px; margin-left: 6px; margin-bottom: 4px;
    border-bottom: 1px dotted var(--rule);
  }

  .locations {
    position: absolute; left: 30px; right: 24px; bottom: 16px;
    list-style: none;
    display: flex; flex-wrap: wrap; gap: 2px 14px;
    font-size: 11px; color: var(--text-dark);
  }
  .locations li { display: flex; align-items: center; gap: 5px; }
  .locations svg { width: 9px; height: 11px; fill: var(--leaf-green); flex: none; }
</style>
</head>
<body>

<section class="card card-front" aria-label="Business card front">
  <div class="brand">
    <span class="brand-dot"></span>
    <span class="brand-name"><span class="brand-main">Brightfield</span><span class="brand-sub">Nutrition &amp; Dietetics</span></span>
  </div>

  <ul class="contact-list">
    <li>0427 561 903 <svg viewBox="0 0 12 12"><path d="M2 1h2.5l1 3-1.5 1a6 6 0 0 0 3 3l1-1.5 3 1V10a1 1 0 0 1-1 1A9 9 0 0 1 1 2a1 1 0 0 1 1-1z"/></svg></li>
    <li>6457 2183 <svg viewBox="0 0 12 12"><path d="M3 0h6v12H3zM4 1.5v8h4v-8z" fill-rule="evenodd"/></svg></li>
    <li>marcus.k.diet@fernmail.com <svg viewBox="0 0 12 12"><path d="M0 2h12v8H0zM1 3l5 3.5L11 3z" fill-rule="evenodd"/></svg></li>
    <li class="gap">www.brightfieldnutrition.com.au <svg viewBox="0 0 12 12"><circle cx="6" cy="6" r="5.5"/></svg></li>
  </ul>

  <div class="person">
    <p class="person-name">Marcus Kellaway</p>
    <p class="person-role">Managing Director</p>
  </div>

  <p class="credential">Certified Clinical Nutritionist and Chef</p>
</section>

<section class="card card-back" aria-label="Business card back">
  <div class="back-band"></div>
  <div class="brand">
    <span class="brand-dot"></span>
    <span class="brand-name"><span class="brand-main">Brightfield</span><span class="brand-sub">Nutrition &amp; Dietetics</span></span>
  </div>

  <ul class="appointment">
    <li>Date: <span class="line"></span></li>
    <li>Time: <span class="line"></span></li>
    <li>Location: <span class="line"></span></li>
  </ul>

  <div class="badge-block">
    <p class="badge-text">Certified<br>Clinical<br>Nutritionist</p>
    <span class="badge-shape"></span>
  </div>

  <ul class="locations" aria-label="Clinic locations">
    <li><svg viewBox="0 0 10 12"><path d="M5 0a4 4 0 0 1 4 4c0 3-4 8-4 8S1 7 1 4a4 4 0 0 1 4-4z"/></svg>Pinebrook Medical Centre</li>
    <li><svg viewBox="0 0 10 12"><path d="M5 0a4 4 0 0 1 4 4c0 3-4 8-4 8S1 7 1 4a4 4 0 0 1 4-4z"/></svg>North Corrin Health</li>
    <li><svg viewBox="0 0 10 12"><path d="M5 0a4 4 0 0 1 4 4c0 3-4 8-4 8S1 7 1 4a4 4 0 0 1 4-4z"/></svg>Hollis Medical</li>
    <li><svg viewBox="0 0 10 12"><path d="M5 0a4 4 0 0 1 4 4c0 3-4 8-4 8S1 7 1 4a4 4 0 0 1 4-4z"/></svg>Ashcombe Doctors Surgery</li>
  </ul>
</section>

</body>
</html>
```